Design a Mobile App for Landscape Businesses

This project is to design the first three screens for a mobile app for Landscape and Lawncare businesses. This app will serve as a directory for homeowners to locate landscape and lawn care businesses and for landscape businesses and contractors to run their business. See the attached PDF for more information and example
Here is the link to the description https://lnkbrev.example/q7z3Kp

Target Market(s)

Landscape and lawn care business, gardeners, home owners

Industry/Entity Type

Landscape Gardening

Logo Text

Verdalink

Colors

Designer to choose colors to be used in the design.

```html
<!DOCTYPE html>
<html lang="en">
<head>
<meta charset="utf-8">
<title>Find a Gardener – Alder's Landscaping</title>
<link rel="stylesheet" href="https://fonts.googleapis.com/css2?family=Montserrat:wght@600;700&family=Mulish:wght@400;600&display=swap">
<style>
:root{
  --ink:#1d2a38;
  --text:#2b3440;
  --muted:#7d8794;
  --teal:#2bb3d6;
  --green:#4fe0a4;
  --band:#eef1f4;
  --line:#e3e7ec;
  --white:#ffffff;
  --alert:#f26a1b;
  --badge:#e7ebef;
}
*{box-sizing:border-box;margin:0;padding:0}
html,body{width:1200px;height:2595px;overflow:hidden;background:var(--white)}
.screen{position:absolute;left:0;top:0;width:375px;height:811px;transform:scale(3.2);transform-origin:0 0;background:var(--white);font-family:'Mulish',sans-serif;color:var(--text);overflow:hidden}
.hero{position:absolute;left:0;top:0;width:375px;height:243px;background:linear-gradient(180deg,#6a5a52 0%,#8b7d6e 28%,#4f6b3c 52%,#6d8f45 72%,#4a7a2e 100%)}
.hero-shade{position:absolute;left:0;top:0;width:375px;height:80px;background:linear-gradient(180deg,rgba(0,0,0,.45),rgba(0,0,0,0))}
.status{position:absolute;top:0;left:0;width:375px;height:24px;color:var(--white);font-size:12px}
.status-time{position:absolute;right:10px;top:4px;font-family:'Montserrat',sans-serif;font-weight:600}
.status-icons{position:absolute;right:48px;top:5px}
.topbar{position:absolute;top:28px;left:0;width:375px;height:24px;color:var(--white)}
.topbar-title{position:absolute;left:38px;top:3px;font-family:'Montserrat',sans-serif;font-weight:700;font-size:15px}
.topbar svg{position:absolute}
.pager{position:absolute;top:226px;left:166px;display:flex;gap:4px}
.pager span{width:8px;height:8px;border-radius:50%;background:rgba(255,255,255,.55)}
.pager span:first-child{background:var(--white)}
.badge{position:absolute;left:276px;top:203px;width:86px;height:86px;border-radius:50%;background:var(--white);padding:6px}
.badge-inner{width:74px;height:74px;border-radius:50%;background:var(--badge)}
.name{position:absolute;left:12px;top:257px;font-family:'Montserrat',sans-serif;font-weight:700;font-size:19.5px;color:var(--ink)}
.contact{position:absolute;left:16px;top:290px;display:flex;gap:14px;font-size:13.5px;color:var(--ink);align-items:center}
.contact-item{display:flex;align-items:center;gap:6px}
.areas{position:absolute;left:15px;top:331px;display:flex;gap:7px}
.chip{height:25px;padding:0 12px 0 10px;border:1.3px solid var(--teal);border-radius:13px;display:flex;align-items:center;gap:5px;font-size:11.5px;color:var(--ink)}
.band{position:absolute;left:0;width:375px;background:var(--band)}
.section-title{position:absolute;left:18px;font-family:'Montserrat',sans-serif;font-weight:700;font-size:12.5px;color:var(--ink)}
.bio-text{position:absolute;left:18px;top:422px;width:350px;font-size:13.4px;line-height:21.5px;color:var(--text);white-space:nowrap}
.services{position:absolute;left:0;top:594px;width:375px;height:81px;border-top:1px solid var(--line);display:flex}
.service{flex:1;display:flex;flex-direction:column;align-items:center;padding-top:20px;gap:6px;font-size:13.4px;color:var(--text);border-right:1px solid var(--line)}
.service:last-child{border-right:none}
.service-icon{width:18px;height:18px;display:flex;align-items:center;justify-content:center}
.cta{position:absolute;left:10px;top:695px;width:354px;height:46px;border-radius:23px;background:linear-gradient(90deg,#33b6df,#50e0a3);color:var(--white);font-family:'Montserrat',sans-serif;font-weight:700;font-size:12.5px;display:flex;align-items:center;justify-content:center;gap:6px;box-shadow:0 3px 8px rgba(60,180,200,.25)}
.tabbar{position:absolute;left:0;top:762px;width:375px;height:49px;background:var(--white);border-top:1px solid var(--line);display:flex}
.tab{flex:1;display:flex;flex-direction:column;align-items:center;padding-top:6px;gap:2px;font-size:10px;color:var(--muted);position:relative}
.tab.active{color:var(--teal)}
.tab-icon{width:20px;height:20px;display:flex;align-items:center;justify-content:center}
.tab-dot{position:absolute;top:6px;left:53px;width:8px;height:8px;border-radius:50%;background:var(--alert)}
</style>
</head>
<body>
<main class="screen">
  <div class="hero" role="img" aria-label="Photo of a landscaped front garden with stone retaining walls, shrubs and lawn before a brick house"></div>
  <div class="hero-shade"></div>

  <div class="status">
    <svg class="status-icons" width="46" height="14" viewBox="0 0 46 14" fill="#fff">
      <circle cx="6" cy="7" r="4.5" fill="none" stroke="#fff" stroke-width="1.4"/>
      <path d="M14 3 L22 3 L18 11 Z"/>
      <path d="M26 12 L34 12 L34 3 Z"/>
      <rect x="38" y="2" width="6" height="11" rx="1"/>
    </svg>
    <span class="status-time">16:54</span>
  </div>

  <div class="topbar">
    <svg style="left:10px;top:3px" width="20" height="18" viewBox="0 0 20 18" fill="none" stroke="#fff" stroke-width="2.2" stroke-linecap="round" stroke-linejoin="round"><path d="M18 9H3M9 2L2 9l7 7"/></svg>
    <span class="topbar-title">Find a Gardener</span>
    <svg style="right:10px;top:0" width="24" height="23" viewBox="0 0 24 23" fill="none" stroke="#fff" stroke-width="1.6" stroke-linejoin="round"><path d="M12 1.5l3.1 6.6 7.2.9-5.3 5 1.4 7.1L12 17.6l-6.4 3.5L7 14l-5.3-5 7.2-.9z"/></svg>
  </div>

  <div class="pager"><span></span><span></span><span></span><span></span></div>

  <div class="badge"><div class="badge-inner"></div></div>

  <h1 class="name">Alder’s Landscaping</h1>
  <div class="contact">
    <span class="contact-item">
      <svg width="11" height="17" viewBox="0 0 11 17" fill="none" stroke="var(--teal)" stroke-width="1.4"><rect x="1" y="1" width="9" height="15" rx="1.6"/><path d="M4 13.2h3"/></svg>
      07700 900 314
    </span>
    <span class="contact-item">
      <svg width="13" height="17" viewBox="0 0 13 17" fill="none" stroke="var(--teal)" stroke-width="1.4"><path d="M6.5 16s5.5-5.6 5.5-9.5a5.5 5.5 0 0 0-11 0C1 10.4 6.5 16 6.5 16z"/><circle cx="6.5" cy="6.5" r="2"/></svg>
      London, UK
    </span>
  </div>

  <div class="areas">
    <span class="chip"><svg width="8" height="11" viewBox="0 0 8 11" fill="var(--teal)"><path d="M4 11S0 6.8 0 4a4 4 0 0 1 8 0c0 2.8-4 7-4 7z"/><circle cx="4" cy="4" r="1.4" fill="#fff"/></svg>Scarborough</span>
    <span class="chip"><svg width="8" height="11" viewBox="0 0 8 11" fill="var(--teal)"><path d="M4 11S0 6.8 0 4a4 4 0 0 1 8 0c0 2.8-4 7-4 7z"/><circle cx="4" cy="4" r="1.4" fill="#fff"/></svg>Whitby</span>
    <span class="chip"><svg width="8" height="11" viewBox="0 0 8 11" fill="var(--teal)"><path d="M4 11S0 6.8 0 4a4 4 0 0 1 8 0c0 2.8-4 7-4 7z"/><circle cx="4" cy="4" r="1.4" fill="#fff"/></svg>Filey</span>
  </div>

  <div class="band" style="top:373px;height:8px"></div>

  <h2 class="section-title" style="top:397px">Bio</h2>
  <p class="bio-text">Experienced and skilled gardener based in<br>Scarborough. I specialise in law care, hedge mae<br>cenas sed diam eget risus varius blandit sit amet non<br>magna. Fusce dapibus, tellus ac cursus commodo,<br>tortor mauris.</p>

  <div class="band" style="top:537px;height:9px"></div>

  <h2 class="section-title" style="top:563px">Services</h2>
  <div class="services">
    <div class="service">
      <span class="service-icon"><svg width="16" height="16" viewBox="0 0 16 16" fill="none" stroke="var(--teal)" stroke-width="1.3" stroke-linecap="round"><path d="M2 15C2 10 1 7 0.8 5M6 15c0-5-1-9-2-12M10 15c0-5 1-9 2-12M14 15c0-4 .8-7 1.2-9M8 15V4"/></svg></span>
      Lawn Care
    </div>
    <div class="service">
      <span class="service-icon"><svg width="16" height="16" viewBox="0 0 16 16" fill="var(--teal)"><path d="M1 15l5-5" stroke="var(--teal)" stroke-width="1.6" stroke-linecap="round"/><path d="M6.5 5.5l4 4-2 2c-1.6 1.2-3.6.2-4-1.2-.5-1.5.4-3.2 2-4.8z"/><path d="M10 6l4-4" stroke="var(--teal)" stroke-width="1.6" stroke-linecap="round"/></svg></span>
      Landscaping
    </div>
    <div class="service">
      <span class="service-icon"><svg width="16" height="18" viewBox="0 0 16 18" fill="none" stroke="var(--teal)" stroke-width="1.3" stroke-linejoin="round"><path d="M8 1L3.5 6.5h2.5L2.5 11h3L1.5 15h13l-4-4h3L10 6.5h2.5z"/><path d="M8 15v2.5"/></svg></span>
      Landscaping
    </div>
  </div>

  <div class="band" style="top:675px;height:87px"></div>
  <a class="cta">Get a Quote
    <svg width="7" height="11" viewBox="0 0 7 11" fill="none" stroke="#fff" stroke-width="1.6" stroke-linecap="round" stroke-linejoin="round"><path d="M1.5 1l4 4.5-4 4.5"/></svg>
  </a>

  <nav class="tabbar">
    <span class="tab active">
      <span class="tab-icon"><svg width="20" height="20" viewBox="0 0 20 20" fill="var(--teal)"><path d="M7 15S2 10 2 6.5a5 5 0 0 1 10 0C12 10 7 15 7 15z"/><circle cx="7" cy="6.5" r="1.8" fill="#fff"/><path d="M15 19s-3.5-3.6-3.5-6a3.5 3.5 0 0 1 7 0c0 2.4-3.5 6-3.5 6z"/></svg></span>
      Search
    </span>
    <span class="tab">
      <span class="tab-icon"><svg width="18" height="18" viewBox="0 0 18 18" fill="none" stroke="var(--muted)" stroke-width="1.3"><rect x="2" y="2" width="3" height="3"/><rect x="2" y="7.5" width="3" height="3"/><rect x="2" y="13" width="3" height="3"/><path d="M8 3.5h8M8 9h8M8 14.5h8"/></svg></span>
      Bookings
    </span>
    <span class="tab">
      <span class="tab-icon"><svg width="20" height="18" viewBox="0 0 20 18" fill="none" stroke="var(--muted)" stroke-width="1.3"><rect x="1" y="3" width="18" height="13" rx="1"/><path d="M1 4l9 7 9-7"/></svg></span>
      <span class="tab-dot"></span>
      Messages
    </span>
    <span class="tab">
      <span class="tab-icon"><svg width="18" height="18" viewBox="0 0 18 18" fill="none" stroke="var(--muted)" stroke-width="1.3"><circle cx="9" cy="9" r="3"/><path d="M9 1v2.5M9 14.5V17M1 9h2.5M14.5 9H17M3.3 3.3l1.8 1.8M12.9 12.9l1.8 1.8M3.3 14.7l1.8-1.8M12.9 5.1l1.8-1.8"/></svg></span>
      Account
    </span>
  </nav>
</main>
</body>
</html>
```